Business Cards for a law firm

Business cards for our law firm. Use our silhoette logo and OAK PARTNERS - check our website (www.oakpartners.example)

Contact Information for Business Card

our silhouette logo, OAK PARTNERS, 800-555-0147, Dorian Pemberton, dorian@oakpartners.example

Requirements
Must have
• our silhouette logo, OAK PARTNERS, 800-555-0147, Dorian Pemberton, dorian@oakpartners.example

```html
<!DOCTYPE html>
<html lang="en">
<head>
<meta charset="utf-8">
<title>Oak Partners – Business Cards</title>
<link href="https://fonts.googleapis.com/css2?family=Overpass:wght@400;700;800&display=swap" rel="stylesheet">
<style>
  :root {
    --navy: #22336c;
    --white: #ffffff;
    --ink: #1b1b1b;
    --backdrop: #e9e9ec;
  }
  * { margin: 0; padding: 0; box-sizing: border-box; }
  html, body {
    width: 1200px; height: 1059px; overflow: hidden;
    background: var(--backdrop);
    font-family: "Overpass", Arial, sans-serif;
  }
  .card { position: absolute; }
  .card--front { left: 256px; top: 100px; width: 688px; height: 391px; background: var(--white); color: var(--navy); }
  .card--back { left: 253px; top: 537px; width: 694px; height: 394px; background: var(--navy); color: var(--white); }

  .brand-mark { position: absolute; }
  .card--front .brand-mark { left: 127px; top: 78px; width: 56px; height: 56px; background: var(--navy); }
  .card--back .brand-mark { left: 97px; top: 166px; width: 64px; height: 64px; background: var(--white); }

  .wordmark {
    position: absolute; white-space: nowrap;
    font-weight: 800; line-height: 1;
  }
  .card--front .wordmark { left: 197px; top: 87px; font-size: 43px; letter-spacing: 3px; }
  .card--back .wordmark { left: 178px; top: 180px; font-size: 50px; letter-spacing: 3.5px; }

  .person { position: absolute; right: 364px; top: 208px; text-align: right; }
  .person__name { font-size: 25px; font-weight: 700; letter-spacing: .3px; line-height: 1; white-space: nowrap; }
  .person__role { margin-top: 10px; font-size: 17px; color: var(--ink); letter-spacing: .5px; line-height: 1; }

  .divider { position: absolute; left: 347px; top: 199px; width: 2px; height: 66px; background: var(--navy); }

  .contacts { position: absolute; left: 378px; top: 191px; list-style: none; }
  .contacts li {
    display: flex; align-items: center; height: 26.5px;
    font-size: 17px; color: var(--ink); white-space: nowrap;
  }
  .contacts svg { width: 15px; height: 15px; margin-right: 10px; fill: var(--navy); flex: none; }

  .address-band {
    position: absolute; left: 0; right: 0; top: 320px; height: 27px;
    background: var(--navy); color: var(--white);
    font-size: 16px; text-align: center; line-height: 29px; letter-spacing: .2px; white-space: nowrap;
  }
</style>
</head>
<body>
  <section class="card card--front">
    <div class="brand-mark" role="img" aria-label="Firm logo mark"></div>
    <div class="wordmark">OAK PARTNERS</div>

    <div class="person">
      <div class="person__name">DORIAN PEMBERTON</div>
      <div class="person__role">OWNER</div>
    </div>
    <div class="divider"></div>

    <ul class="contacts">
      <li>
        <svg viewBox="0 0 24 24" aria-hidden="true"><path d="M6.6 10.8a15 15 0 0 0 6.6 6.6l2.2-2.2a1 1 0 0 1 1-.25 11.4 11.4 0 0 0 3.6.57 1 1 0 0 1 1 1V20a1 1 0 0 1-1 1A17 17 0 0 1 3 4a1 1 0 0 1 1-1h3.5a1 1 0 0 1 1 1c0 1.250.2 2.450.57 3.570a1 1 0 0 1-.25 1z"/></svg>
        800-555-0147
      </li>
      <li>
        <svg viewBox="0 0 24 24" aria-hidden="true"><path d="M3 5h18v14H3zm2 2v10h14V7l-7 5z"/></svg>
        dorian@oakpartners.example
      </li>
      <li>
        <svg viewBox="0 0 24 24" aria-hidden="true"><path d="M12 2a10 10 0 1 0 0 20 10 10 0 0 0 0-20zm-1 17.9A8 8 0 0 1 4.1 11H8a13 13 0 0 0 3 8.9zM13 4.1A8 8 0 0 1 19.9 11H16a13 13 0 0 0-3-6.9zM10 11a11 11 0 0 1 2-6 11 11 0 0 1 2 6zm0 2h4a11 11 0 0 1-2 6 11 11 0 0 1-2-6z"/></svg>
        www.oakpartners.example
      </li>
    </ul>

    <div class="address-band">1450 Harbor Ave #310, Lakeview, CA 90000</div>
  </section>

  <section class="card card--back">
    <div class="brand-mark" role="img" aria-label="Firm logo mark"></div>
    <div class="wordmark">OAK PARTNERS</div>
  </section>
</body>
</html>
```